Bluecrest Learning Corps by graduating students from college in two years

Based on the logo design, create stationary and business cards for
Dr. Venrel T Oskamp, CEO, (703) 482-1736
and Marisa Deltoft, Respresentative, (301) 647-2208
Address: 4719 Pellham Court, Harlow Station, VA 22081
Incorporate elelments of the logo

Target Market(s)

USA

Font styles to use
Other font styles liked:
• match with the logo type style

```html
<!DOCTYPE html>
<html lang="en">
<head>
<meta charset="utf-8">
<title>Bluecrest Learning Corps — Stationery</title>
<link rel="stylesheet" href="https://fonts.googleapis.com/css2?family=Crimson+Pro:wght@400;600&display=swap">
<style>
  :root {
    --navy: #1d2a5c;
    --gold: #efb82a;
    --gold-soft: rgba(239, 184, 42, 0);
    --paper: #ffffff;
    --backdrop: #e4e5e4;
    --serif: "Crimson Pro", Georgia, serif;
  }
  * { box-sizing: border-box; margin: 0; padding: 0; }
  html, body { width: 1200px; height: 1200px; overflow: hidden; }
  body { background: var(--backdrop); font-family: var(--serif); color: var(--navy); position: relative; }

  .letterhead {
    position: absolute; left: 137px; top: 128px; width: 715px; height: 944px;
    background: var(--paper); box-shadow: 0 2px 8px rgba(0,0,0,.12);
  }
  .rule { position: absolute; height: 3px; background: var(--gold); }

  .brand-mark {
    position: absolute; left: 43px; top: 30px; width: 160px; height: 160px;
    border-radius: 50%; border: 5px solid var(--gold);
  }
  .brand-name {
    position: absolute; left: 222px; top: 56px; width: 250px;
    font-weight: 600; font-size: 30px; line-height: 40px; letter-spacing: 0.5px;
    text-transform: uppercase; color: var(--navy); white-space: nowrap;
  }

  .footer-line { position: absolute; left: 284px; top: 876px; width: 388px; height: 2px; background: var(--gold); }
  .footer-contact {
    position: absolute; top: 884px; font-size: 17px; line-height: 21px; color: var(--navy);
    display: flex; gap: 7px;
  }
  .footer-contact svg { width: 15px; height: 17px; flex: none; margin-top: 2px; }
  .footer-phones { display: flex; flex-direction: column; }
  .footer-phones div { display: flex; gap: 8px; align-items: center; }

  .card {
    position: absolute; left: 702px; width: 284px; height: 164px;
    background: var(--paper); box-shadow: -6px 8px 14px rgba(0,0,0,.14);
  }
  .card-top { position: absolute; right: 0; height: 2px; width: 134px;
    background: linear-gradient(to left, var(--gold), var(--gold) 60%, var(--gold-soft)); }
  .card-bottom { position: absolute; left: 0; height: 2px; width: 132px;
    background: linear-gradient(to right, var(--gold), var(--gold) 60%, var(--gold-soft)); }
  .card-mark {
    position: absolute; left: 12px; top: 30px; width: 104px; height: 104px; border-radius: 50%;
    border: 4px solid var(--gold); display: flex; align-items: center; justify-content: center;
    text-align: center; font-size: 12px; line-height: 14px; padding: 10px;
  }
  .card-name { position: absolute; left: 139px; top: 52px; font-size: 15px; line-height: 17px; white-space: nowrap; }
  .card-title { position: absolute; left: 138px; top: 70px; font-size: 11.5px; }
  .card-contact { position: absolute; left: 138px; top: 112px; font-size: 10px; line-height: 14px; white-space: nowrap; }
  .card-contact .row { display: flex; gap: 4px; align-items: flex-start; }
  .card-contact svg { width: 9px; height: 10px; flex: none; margin-top: 2px; }
  .card-contact .indent { padding-left: 13px; }
</style>
</head>
<body>

<svg width="0" height="0" style="position:absolute">
  <defs>
    <symbol id="icon-pin" viewBox="0 0 16 20">
      <path fill="#1d2a5c" d="M8 0C3.6 0 0 3.4 0 7.6 0 13 8 20 8 20s8-7 8-12.4C16 3.4 12.4 0 8 0zm0 10.5A3 3 0 1 1 8 4.5a3 3 0 0 1 0 6z"/>
    </symbol>
    <symbol id="icon-phone" viewBox="0 0 20 20">
      <path fill="#1d2a5c" d="M4.2 0.8l3 3.6c.5.6.4 1.4-.1 1.9L5.6 7.7c1.2 2.7 3.6 5.1 6.3 6.4l1.5-1.5c.5-.5 1.3-.6 1.9-.1l3.6 3c.6.5.7 1.4.1 2l-1.6 1.7C15.9 20.4 14 20.5 12 19.5 6.8 17 3 13.2.5 8 -.5 6 -.4 4.1 1.1 2.6L2.8.7c.4-.5 1-.5 1.4.1z"/>
    </symbol>
  </defs>
</svg>

<section class="letterhead" aria-label="Letterhead">
  <div class="rule" style="left:0;top:83px;width:33px"></div>
  <div class="rule" style="left:0;top:94px;width:33px"></div>
  <div class="rule" style="left:0;top:105px;width:33px"></div>

  <div class="brand-mark"></div>
  <h1 class="brand-name">Bluecrest<br>Learning Corps</h1>

  <div class="rule" style="left:492px;top:83px;width:223px"></div>
  <div class="rule" style="left:492px;top:94px;width:223px"></div>
  <div class="rule" style="left:492px;top:105px;width:223px"></div>

  <div class="rule" style="left:0;top:895px;width:268px"></div>
  <div class="rule" style="left:0;top:906px;width:268px"></div>
  <div class="footer-line"></div>

  <div class="footer-contact" style="left:284px">
    <svg><use href="#icon-pin"/></svg>
    <address style="font-style:normal">4719 Pellham Court,<br>Harlow Station, VA 22081</address>
  </div>
  <div class="footer-contact" style="left:540px">
    <div class="footer-phones">
      <div><svg><use href="#icon-phone"/></svg>(703) 482-1736</div>
      <div><svg><use href="#icon-phone"/></svg>(301) 647-2208</div>
    </div>
  </div>
</section>

<section class="card" style="top:382px" aria-label="Business card, Dr. Venrel T Oskamp">
  <div class="card-top" style="top:19px"></div>
  <div class="card-top" style="top:25px"></div>
  <div class="card-top" style="top:32px"></div>
  <div class="card-mark">Bluecrest Learning Corps</div>
  <p class="card-name">Dr. Venrel T Oskamp</p>
  <p class="card-title">CEO</p>
  <div class="card-contact">
    <div class="row"><svg><use href="#icon-pin"/></svg>4719 Pellham Court,</div>
    <div class="indent">Harlow Station, VA 22081</div>
    <div class="row"><svg><use href="#icon-phone"/></svg>(703) 482-1736</div>
  </div>
  <div class="card-bottom" style="top:143px"></div>
  <div class="card-bottom" style="top:150px"></div>
  <div class="card-bottom" style="top:157px"></div>
</section>

<section class="card" style="top:593px" aria-label="Business card, Marisa Deltoft">
  <div class="card-top" style="top:19px"></div>
  <div class="card-top" style="top:25px"></div>
  <div class="card-top" style="top:32px"></div>
  <div class="card-mark">Bluecrest Learning Corps</div>
  <p class="card-name">Marisa Deltoft</p>
  <p class="card-title">Respresentative</p>
  <div class="card-contact">
    <div class="row"><svg><use href="#icon-pin"/></svg>4719 Pellham Court,</div>
    <div class="indent">Harlow Station, VA 22081</div>
    <div class="row"><svg><use href="#icon-phone"/></svg>(301) 647-2208</div>
  </div>
  <div class="card-bottom" style="top:143px"></div>
  <div class="card-bottom" style="top:150px"></div>
  <div class="card-bottom" style="top:157px"></div>
</section>

</body>
</html>
```